Plakate für Haushaltshilfen und Alltagsbegleiter
Zielgruppe
Wir bieten haushaltsnahe Dienstleistungen (Haushaltshilfen und Altgasbegleiter) für Personen mit einem Pflegegrad 1 - 5 an.
Zielgruppe sind Personen mit einem Pflegegrad 1 - 5. Hauptsächlich ältere Menschen die Unterstützung/Betreuung im Alltag und Haushalt benötigen.
Aufgabenstellung
Wir benötigen für unsere Büroräume eine Fensterbeschriftung. Es handelt sich hier um 5 Fenster (Glasflächen) und eine Glastür. Die Vorgabe ist, dass von außen zu erkennen ist dass sich um alle Räumlichkeiten um unsere (Firma Lindwerk) Räumlichkeiten handelt. Desweiteren soll auch unser Angebot erkennbar sein.
Unser Angebot enthält: Haushaltshilfen und Alltagsbegleiter
- kostenlose Haushaltshilfe ab Pflegegrad 1
- Abrechnung mit allen Kostenträgern
Da wir keine Schilder an die Fassade anbringen können, müßen die Glasflächen dafür genutzt werden um zum Einen uns als Firma erkennbar zu machen und zum anderen unser Angebot kurz zu präsentieren.
Uns ist wichtig dass unser Logo verwendet wir und auch unsere Farben.
Desweiteren sollten an den Fenstern auch teilweise eine Sichtschutz nach innen, angebracht werden, aber eben nur teilweise also nicht das ganzen Fenster z.Bsp. mit einer Blickdichten Folie überziehen, sondern in Augenhöhe wenn Fußgänger vorbei laufen.

```html
<!DOCTYPE html>
<html lang="de">
<head>
<meta charset="utf-8">
<title>Lindwerk – Fensterbeschriftung</title>
<link rel="stylesheet" href="https://fonts.googleapis.com/css2?family=Cinzel:wght@400;600&display=swap">
<style>
  :root {
    --bg: #eeece8;
    --glass: #1c1d1f;
    --glass-edge: #2a2b2e;
    --brand-red: #c8081b;
    --ink-light: #ffffff;
  }
  * { margin: 0; padding: 0; box-sizing: border-box; }
  html, body { width: 1200px; height: 827px; overflow: hidden; background: var(--bg); }
  .canvas { position: relative; width: 1200px; height: 827px; }
  .pane { position: absolute; background: var(--glass); border: 3px solid var(--glass-edge); overflow: hidden; }
  .pane svg { display: block; width: 100%; height: 100%; }
  .pane--window-left { left: 130px; top: 160px; width: 300px; height: 480px; }
  .pane--door { left: 470px; top: 100px; width: 260px; height: 660px; }
  .pane--window-right { left: 770px; top: 160px; width: 300px; height: 480px; }
  .brand-text { font-family: "Cinzel", serif; }
</style>
</head>
<body>
<main class="canvas">

  <section class="pane pane--window-left" aria-label="Fenster Fensterreinigung">
    <svg viewBox="0 0 300 480" class="brand-text">
      <circle class="brand-dot" cx="150" cy="58" r="36" fill="none" stroke="var(--brand-red)" stroke-width="4"/>
      <rect class="service-band" x="0" y="112" width="300" height="52" fill="var(--brand-red)"/>
      <text x="150" y="146" text-anchor="middle" fill="var(--ink-light)" font-size="22" letter-spacing="1">FENSTERREINIGUNG</text>
      <circle class="accent-dot" cx="58" cy="360" r="22" fill="var(--brand-red)"/>
      <circle class="accent-ring" cx="285" cy="440" r="150" fill="none" stroke="var(--brand-red)" stroke-width="4"/>
      <circle class="service-badge" cx="290" cy="445" r="128" fill="var(--brand-red)" role="img" aria-label="Symbol Fensterabzieher mit Glanzsternen"/>
    </svg>
  </section>

  <section class="pane pane--door" aria-label="Glastür Lindwerk">
    <svg viewBox="0 0 260 660" class="brand-text">
      <circle class="brand-dot" cx="130" cy="115" r="30" fill="none" stroke="var(--brand-red)" stroke-width="4"/>
      <text x="130" y="190" text-anchor="middle" fill="var(--ink-light)" font-size="30" font-weight="600" letter-spacing="1">LINDWERK</text>
      <text x="130" y="205" text-anchor="middle" fill="var(--brand-red)" font-size="8" letter-spacing="0.5">HAUSHALTSHILFEN &amp; MEHR</text>
      <text x="130" y="330" text-anchor="middle" fill="var(--ink-light)" font-size="15">HAUSHALTSHILFEN &amp;</text>
      <text x="130" y="356" text-anchor="middle" fill="var(--ink-light)" font-size="15">ALLTAGSBEGLEITER</text>
      <text x="130" y="540" text-anchor="middle" fill="var(--brand-red)" font-size="15">0711 98 76 5432</text>
      <text x="130" y="566" text-anchor="middle" fill="var(--brand-red)" font-size="15">INFO@LINDWERK.DE</text>
      <rect class="door-handle" x="222" y="300" width="6" height="200" rx="3" fill="#8a8c90"/>
    </svg>
  </section>

  <section class="pane pane--window-right" aria-label="Fenster Kehrwoche">
    <svg viewBox="0 0 300 480" class="brand-text">
      <circle class="brand-dot" cx="150" cy="58" r="36" fill="none" stroke="var(--brand-red)" stroke-width="4"/>
      <rect class="service-band" x="0" y="112" width="300" height="52" fill="var(--brand-red)"/>
      <text x="150" y="146" text-anchor="middle" fill="var(--ink-light)" font-size="22" letter-spacing="1">KEHRWOCHE</text>
      <circle class="accent-dot" cx="140" cy="280" r="20" fill="var(--brand-red)"/>
      <circle class="accent-dot" cx="60" cy="370" r="38" fill="var(--brand-red)"/>
      <circle class="accent-ring" cx="285" cy="440" r="150" fill="none" stroke="var(--brand-red)" stroke-width="4"/>
      <circle class="service-badge" cx="290" cy="445" r="128" fill="var(--brand-red)" role="img" aria-label="Symbol Besen mit Staub"/>
    </svg>
  </section>

</main>
</body>
</html>
```